13 Varno - new website design project

Our company Varno Electrical is developing a new lead generation website focused on Electrical, LED Lighting and Solar Power. We need a high converting website.

Example of our current website is www.varnoelectrical-example.com.au You can take content from this website for this new design. Our colours are red, black and white. For our new website we would like to promote Varno, Spark Every Day. Please listen to the jingle.

The below link is the company jingle that we have developed.
http://www.tunecraftdemo.com.au/vrn-tc-v1/

The key for this brief is to generate leads for Electrical, LED Lighting (for commercial) and Solar Power & Storage.

Target Market(s)

Business owners in Melbourne Victoria

Number of Pages Required

4 page

Colors
ec1f27
ffffff

Requirements
Must have
• This page must be clean, be in line with company branding and a high converting lead website.

```html
<!DOCTYPE html>
<html lang="en">
<head>
<meta charset="utf-8">
<title>Varno Electrical</title>
<link rel="stylesheet" href="https://fonts.googleapis.com/css2?family=Lato:wght@400;700;900&family=Roboto:wght@400;500;700&display=swap">
<style>
:root{
  --red:#ec1f27;
  --red-dark:#c8151c;
  --ink:#222222;
  --text:#444444;
  --muted:#666666;
  --light:#f0f0f0;
  --line:#dddddd;
  --white:#ffffff;
  --dark:#1d1d1f;
}
*{box-sizing:border-box;margin:0;padding:0}
html,body{width:1200px;height:3169px;overflow:hidden}
body{position:relative;background:var(--white);font-family:"Lato",sans-serif;color:var(--text)}
.abs{position:absolute}

/* header */
.site-header{left:0;top:0;width:1200px;height:142px;background:var(--white);border-top:3px solid var(--red)}
.brand{left:98px;top:30px;display:flex;align-items:center;gap:12px}
.brand-mark{width:46px;height:46px;border-radius:50%;background:var(--red)}
.brand-name{font-family:"Lato",sans-serif;font-weight:900;font-size:44px;color:var(--ink);line-height:1}
.brand-tag{left:158px;top:94px;font-family:"Lato",sans-serif;font-size:15px;color:var(--red);font-style:italic}
.top-contact{left:565px;top:28px;display:flex;align-items:center;font-family:"Roboto",sans-serif;font-size:17px;color:var(--ink)}
.top-contact .ic{width:34px;height:34px;border-radius:50%;display:inline-flex;align-items:center;justify-content:center;margin-right:8px}
.top-contact .mail{background:var(--red)}
.top-contact .phone{background:#333;margin-left:34px}
.top-contact .email-text{color:var(--red)}
.socials{left:962px;top:32px;display:flex;gap:6px}
.socials span{width:22px;height:22px;background:#9a9a9a;border-radius:3px}
.socials span:last-child{background:var(--red)}
.main-nav{left:450px;top:94px;display:flex;gap:35px;font-family:"Roboto",sans-serif;font-weight:500;font-size:15px;color:var(--ink)}
.main-nav .active{color:var(--red)}

/* hero */
.hero{left:0;top:142px;width:1200px;height:520px;background:linear-gradient(100deg,#3a2f26 0%,#6b5236 35%,#8a6a3e 60%,#5a4a30 80%,#c19a2e 100%)}
.hero-shade{left:0;top:142px;width:1200px;height:520px;background:rgba(0,0,0,.38)}
.hero-title{left:0;top:262px;width:1200px;text-align:center;font-family:"Lato",sans-serif;font-weight:700;font-size:60px;color:var(--white);letter-spacing:.5px}
.hero-points{left:0;top:370px;width:1200px;text-align:center;font-family:"Lato",sans-serif;font-weight:700;font-size:29px;color:var(--white);word-spacing:2px}
.hero-points span{margin:0 16px}
.hero-arrow{top:345px}
.hero-curve{left:0;top:560px}

/* services */
.service-photo{width:250px;height:250px;border-radius:50%;border:10px solid var(--red);box-shadow:0 0 0 5px rgba(236,31,39,.35)}
.service{width:320px;text-align:center}
.service h3{font-family:"Lato",sans-serif;font-weight:400;font-size:21px;color:var(--red);margin-bottom:12px}
.service p{font-size:13.5px;line-height:21px;color:var(--text)}
.read-more{display:inline-block;margin-top:16px;font-size:13.5px;color:var(--red)}

/* story */
.story-band{left:0;top:1010px;width:1200px;height:410px;background:var(--light)}
.story-title{left:98px;top:1052px;font-family:"Lato",sans-serif;font-weight:700;font-size:29px;color:var(--red)}
.story-rule{left:98px;top:1090px;width:150px;height:2px;background:var(--red)}
.story-text{left:98px;top:1124px;width:586px;font-size:13px;line-height:22px;color:var(--text);text-align:justify}
.story-text p+p{margin-top:10px}
.btn{display:inline-block;height:42px;line-height:38px;padding:0 16px;font-size:14px;border:2px solid var(--red);border-radius:2px}
.btn-red{background:var(--red);color:var(--white)}
.btn-line{border-color:#333;color:var(--ink);margin-left:10px}
.story-buttons{left:98px;top:1310px}
.story-photo{left:723px;top:1067px;width:376px;height:286px;border:5px solid #cfcfcf;background:linear-gradient(180deg,#7d8c8e 0%,#5f7a5a 45%,#3f6a3a 62%,#3a5f8a 78%,#6e8c5a 100%)}

/* why */
.section-title{left:0;width:1200px;text-align:center;font-family:"Lato",sans-serif;font-weight:700;font-size:29px}
.title-rule{left:540px;width:120px;height:2px;background:var(--red)}
.why-item{width:200px;text-align:center}
.why-item svg{display:block;margin:0 auto}
.why-item h4{margin-top:10px;font-family:"Lato",sans-serif;font-weight:400;font-size:16px;color:var(--ink)}
.why-item.featured h4{color:var(--red)}
.why-item p{margin-top:14px;font-size:12px;line-height:19px;color:var(--muted)}

/* testimonials */
.testimonials{left:0;top:1940px;width:1200px;height:484px;background:linear-gradient(180deg,#232325,#141416)}
.testimonial{width:470px;color:var(--white)}
.avatar{width:120px;height:120px;border-radius:50%;border:5px solid var(--white);background:linear-gradient(180deg,#8c9aa6,#3c4650)}
.quote-mark{font-family:"Lato",sans-serif;font-weight:900;font-size:56px;line-height:1;color:var(--white)}
.t-name{font-family:"Roboto",sans-serif;font-weight:500;font-size:19px}
.t-place{font-family:"Roboto",sans-serif;font-size:15px;color:#dcdcdc}
.stars{font-size:17px;letter-spacing:3px;color:var(--white)}
.t-text{font-size:13.5px;line-height:24px;color:#e6e6e6;text-align:justify}

/* clients */
.clients{left:0;top:2424px;width:1200px;height:344px;background:#efefef}
.client-box{top:2594px;width:148px;height:100px;background:var(--white);border:1px solid #e0e0e0;display:flex;align-items:center;justify-content:center;gap:8px;font-family:"Lato",sans-serif;font-weight:700;font-size:17px;color:var(--ink)}
.client-box .dot{width:14px;height:14px;background:var(--red)}

/* footer */
.footer{left:0;top:2768px;width:1200px;height:338px;background:linear-gradient(135deg,#f4f4f2 0%,#ecece8 50%,#f2f2ef 100%)}
.f-head{font-family:"Roboto",sans-serif;font-weight:500;font-size:16px;color:var(--red)}
.f-rule{width:70px;height:2px;background:var(--red);margin-top:8px}
.f-links{list-style:none;margin-top:20px;font-size:14px;color:var(--ink)}
.f-links li{line-height:32px}
.f-contact{display:flex;gap:14px;margin-top:18px}
.f-contact .pin{width:38px;height:38px;border-radius:50%;border:2px solid var(--red);display:flex;align-items:center;justify-content:center;flex:none}
.f-contact .lbl{font-family:"Roboto",sans-serif;font-weight:700;font-size:14px;color:var(--ink)}
.f-contact .val{font-size:12.5px;line-height:18px;color:var(--text)}
.field{background:var(--white);border:1px solid #cccccc;font-size:11px;color:#555;padding:6px 10px}
.send{background:var(--red);color:var(--white);font-family:"Roboto",sans-serif;font-size:13px;padding:0 14px;height:38px;line-height:38px;border-radius:2px}
.copy-bar{left:0;top:3106px;width:1200px;height:63px;background:#e4e4e4}
.copy-text{left:98px;top:3128px;font-size:14px;color:var(--ink)}
.copy-socials{left:900px;top:3118px;display:flex;gap:10px}
.copy-socials span{width:32px;height:32px;border-radius:50%;border:2px solid #333}
</style>
</head>
<body>

<header class="abs site-header">
  <div class="abs brand"><span class="brand-mark"></span><span class="brand-name">Varno</span></div>
  <div class="abs brand-tag">Spark Every Day</div>
  <div class="abs top-contact">
    <span class="ic mail"><svg width="16" height="12" viewBox="0 0 16 12"><rect x="1" y="1" width="14" height="10" fill="none" stroke="#fff" stroke-width="1.6"/><path d="M1 1l7 6 7-6" fill="none" stroke="#fff" stroke-width="1.6"/></svg></span>
    <span class="email-text">service@varnoelectrical-example.com.au</span>
    <span class="ic phone"><svg width="16" height="16" viewBox="0 0 16 16"><path d="M3 1h3l1.5 4-2 1.3a9 9 0 0 0 4.2 4.2L11 8.5l4 1.5v3a2 2 0 0 1-2 2A13 13 0 0 1 1 3a2 2 0 0 1 2-2z" fill="#fff"/></svg></span>
    <span>139 406</span>
  </div>
  <div class="abs socials"><span></span><span></span><span></span><span></span><span></span></div>
  <nav class="abs main-nav">
    <span class="active">HOME</span><span>VARNO STORY</span><span>OUR WORK</span><span>ELECTRICAL</span><span>LED LIGHTING</span><span>CONTACT US</span>
  </nav>
</header>

<div class="abs hero" role="img" aria-label="Electrician working at an industrial switchboard"></div>
<div class="abs hero-shade"></div>
<h1 class="abs hero-title">VARNO ELECTRICAL</h1>
<div class="abs hero-points"><span>• ELECTRICAL</span><span>• LED LIGHTING</span><span>• SOLAR POWER</span></div>
<svg class="abs hero-arrow" style="left:34px" width="30" height="54" viewBox="0 0 30 54"><path d="M26 2L4 27l22 25" fill="none" stroke="#fff" stroke-width="2.5"/></svg>
<svg class="abs hero-arrow" style="left:1136px" width="30" height="54" viewBox="0 0 30 54"><path d="M4 2l22 25L4 52" fill="none" stroke="#fff" stroke-width="2.5"/></svg>
<svg class="abs hero-curve" width="1200" height="110" viewBox="0 0 1200 110"><path d="M0 110 L0 70 Q600 -20 1200 70 L1200 110 Z" fill="#fff"/></svg>

<!-- services -->
<div class="abs service-photo" style="left:137px;top:540px;background:linear-gradient(150deg,#e8e1d4,#6d7a86 55%,#2e3a48)" role="img" aria-label="Electrician inspecting a switchboard"></div>
<div class="abs service-photo" style="left:481px;top:540px;background:radial-gradient(circle at 45% 40%,#9fb6c0,#3d5a66 55%,#1c2c34)" role="img" aria-label="LED light bulbs"></div>
<div class="abs service-photo" style="left:828px;top:540px;background:linear-gradient(160deg,#cfe0ee 0%,#e6e6e6 30%,#3a5c9a 60%,#233e6e)" role="img" aria-label="Installer fitting solar panels on a roof"></div>

<div class="abs service" style="left:102px;top:812px">
  <h3>ELECTRICAL</h3>
  <p>Great value for money, great service and reliability. These are the key foundations that we offer to our customers.</p>
  <span class="read-more">READ MORE &nbsp;➜</span>
</div>
<div class="abs service" style="left:446px;top:812px">
  <h3>LED LIGHTING</h3>
  <p>Upgrading your business to LED Lighting is one of the quickest ways to slash the operating costs of your business.</p>
  <span class="read-more">READ MORE &nbsp;➜</span>
</div>
<div class="abs service" style="left:793px;top:812px">
  <h3>SOLAR POWER</h3>
  <p>When upgrading your business to LED lights, Varno Electrical will confirm the VEET eligibility and provide cost effective way.</p>
  <span class="read-more">READ MORE &nbsp;➜</span>
</div>

<!-- story -->
<section class="abs story-band"></section>
<h2 class="abs story-title">The Varno Story</h2>
<div class="abs story-rule"></div>
<div class="abs story-text">
  <p>Electrical and Energy Solutions are at the forefront of our company. Varno Electrical has a long history in Electrical, LED Lighting and Solar Power and just like the Cougar, we will strive to be fierce &amp; agile in an effort to exceed our customer's expectations and develop stronger links with all our business partners &amp; community.</p>
  <p>Varno Electrical is an expert Electrical Company providing services to all Residential and Commercial customers. With over 10 years of experience, Varno Electrical has developed.</p>
</div>
<div class="abs story-buttons"><span class="btn btn-red">Read More</span><span class="btn btn-line">Contact Us</span></div>
<div class="abs story-photo" role="img" aria-label="Solar farm in a green mountain valley"></div>

<!-- why choose us -->
<h2 class="abs section-title" style="top:1478px;color:var(--red)">Why Choose Us</h2>
<div class="abs title-rule" style="top:1530px"></div>

<div class="abs why-item" style="left:86px;top:1590px">
  <svg width="150" height="160" viewBox="0 0 150 160"><path d="M75 152 L58 138 A68 68 0 1 1 92 138 Z" fill="#fff" stroke="#333" stroke-width="2.5"/><circle cx="75" cy="62" r="14" fill="none" stroke="#333" stroke-width="7" stroke-dasharray="6 4"/><circle cx="75" cy="62" r="5" fill="#333"/><path d="M44 92h22l14 6 20-8 6 6-26 14H44z" fill="#333"/></svg>
  <h4>Professional service</h4>
  <p>When you hire a Varno Electrical Electrician you will get a professional and well-presented.</p>
</div>
<div class="abs why-item featured" style="left:291px;top:1590px">
  <svg width="150" height="160" viewBox="0 0 150 160"><path d="M75 152 L58 138 A68 68 0 1 1 92 138 Z" fill="#ec1f27" stroke="#ec1f27" stroke-width="2.5"/><circle cx="75" cy="70" r="30" fill="none" stroke="#fff" stroke-width="4" stroke-dasharray="5 3"/><circle cx="75" cy="70" r="20" fill="#fff"/><path d="M66 72l6 6 12-12" fill="none" stroke="#ec1f27" stroke-width="4"/></svg>
  <h4>5 Year Guarantee</h4>
  <p>You can buy with confidence as all of our work has a 5 year workmanship guarantee.</p>
</div>
<div class="abs why-item" style="left:502px;top:1590px">
  <svg width="150" height="160" viewBox="0 0 150 160"><path d="M75 152 L58 138 A68 68 0 1 1 92 138 Z" fill="#fff" stroke="#333" stroke-width="2.5"/><circle cx="75" cy="58" r="18" fill="#333"/><text x="75" y="65" text-anchor="middle" font-family="Lato,sans-serif" font-weight="900" font-size="20" fill="#fff">$</text><path d="M42 90h24l14 6 22-8 6 6-28 14H42z" fill="#333"/></svg>
  <h4>Value For Money</h4>
  <p>We provide extremely competitive pricing, which means you get value for money on quality.</p>
</div>
<div class="abs why-item" style="left:711px;top:1590px">
  <svg width="150" height="160" viewBox="0 0 150 160"><path d="M75 152 L58 138 A68 68 0 1 1 92 138 Z" fill="#fff" stroke="#333" stroke-width="2.5"/><path d="M62 40l8 8-4 12 12 12-6 6-12-12-12 4-8-8 8-2 4-8z" fill="#333"/><path d="M88 40l4 4-10 14 4 4-4 4-18 18-6-6 18-18 4 4z" fill="#333"/><path d="M40 96h24l14 6 22-8 6 6-28 14H40z" fill="#333"/></svg>
  <h4>Environmentally Friendly</h4>
  <p>We a committed to reducing carbon emissions by installing Solar Power.</p>
</div>
<div class="abs why-item" style="left:914px;top:1590px">
  <svg width="150" height="160" viewBox="0 0 150 160"><path d="M75 152 L58 138 A68 68 0 1 1 92 138 Z" fill="#fff" stroke="#333" stroke-width="2.5"/><path d="M50 66a25 22 0 0 1 50 0z" fill="#333"/><path d="M75 44v-6M75 66v14a4 4 0 0 1-8 0" fill="none" stroke="#333" stroke-width="3"/><path d="M42 94h24l14 6 22-8 6 6-28 14H42z" fill="#333"/></svg>
  <h4>Fully Insured</h4>
  <p>Varno Electrical is fully insured and equipped to handle breakdowns and service call outs.</p>
</div>

<!-- testimonials -->
<section class="abs testimonials" role="img" aria-label="Dark background of solar panels at dusk"></section>
<h2 class="abs section-title" style="top:1994px;color:var(--white);font-weight:400">Our Testimonials</h2>
<div class="abs title-rule" style="top:2046px"></div>

<div class="abs avatar" style="left:126px;top:2128px" role="img" aria-label="Client workshop photo"></div>
<div class="abs quote-mark" style="left:270px;top:2102px">“</div>
<div class="abs t-name" style="left:308px;top:2150px;color:#fff">Marcus T.</div>
<div class="abs t-place" style="left:308px;top:2183px">Ashvale North VIC</div>
<div class="abs stars" style="left:308px;top:2213px">★★★★☆</div>
<p class="abs t-text" style="left:98px;top:2306px;width:470px">Excellent work and very professional. Daniel takes time to explain everything and demonstrate workings. Very clear precise and accurate.”</p>

<div class="abs avatar" style="left:664px;top:2128px" role="img" aria-label="Client storefront photo"></div>
<div class="abs quote-mark" style="left:808px;top:2102px">“</div>
<div class="abs t-name" style="left:846px;top:2150px;color:#fff">Elena R.</div>
<div class="abs t-place" style="left:846px;top:2183px">Ashvale VIC</div>
<div class="abs stars" style="left:846px;top:2213px">★★★★☆</div>
<p class="abs t-text" style="left:640px;top:2306px;width:470px">I found Daniel to be well organised, punctual, professional and a good communicator. He did the job at a very reasonable price.</p>

<!-- clients -->
<section class="abs clients"></section>
<h2 class="abs section-title" style="top:2476px;color:var(--red);font-weight:400">Our satisfied clients include...</h2>
<div class="abs title-rule" style="top:2528px"></div>
<div class="abs client-box" style="left:190px"><span class="dot"></span>Lumora</div>
<div class="abs client-box" style="left:416px"><span class="dot"></span>Outback Depot</div>
<div class="abs client-box" style="left:640px"><span class="dot"></span>Heron Supplies</div>
<div class="abs client-box" style="left:862px"><span class="dot"></span>Goldbun</div>

<!-- footer -->
<footer class="abs footer" role="img" aria-label="Faint map of Australia in the background"></footer>
<div class="abs brand" style="left:108px;top:2864px"><span class="brand-mark"></span><span class="brand-name">Varno</span></div>
<div class="abs brand-tag" style="left:168px;top:2928px">Spark Every Day</div>

<div class="abs" style="left:342px;top:2820px">
  <div class="f-head">QUICK LINKS</div><div class="f-rule"></div>
  <ul class="f-links"><li>› Home</li><li>› Varno Story</li><li>› Our Work</li><li>› Electrical</li><li>› LED Lighting</li><li>› Contact Us</li></ul>
</div>

<div class="abs" style="left:518px;top:2820px;width:260px">
  <div class="f-head">CONTACT US</div><div class="f-rule"></div>
  <div class="f-contact"><span class="pin"><svg width="14" height="18" viewBox="0 0 14 18"><path d="M7 17S1 10 1 6.5a6 6 0 0 1 12 0C13 10 7 17 7 17z" fill="none" stroke="#ec1f27" stroke-width="2"/><circle cx="7" cy="6.5" r="2" fill="#ec1f27"/></svg></span><div><div class="lbl">ADDRESS,</div><div class="val">12/84 HARLOW RD<br>ASHVALE, VIC 3150</div></div></div>
  <div class="f-contact"><span class="pin"><svg width="12" height="18" viewBox="0 0 12 18"><rect x="1.5" y="1" width="9" height="16" rx="2" fill="none" stroke="#ec1f27" stroke-width="2"/></svg></span><div><div class="lbl">PHONE:</div><div class="val">139 406</div></div></div>
  <div class="f-contact"><span class="pin" style="background:var(--red)"><svg width="16" height="12" viewBox="0 0 16 12"><rect x="1" y="1" width="14" height="10" fill="none" stroke="#fff" stroke-width="1.6"/><path d="M1 1l7 6 7-6" fill="none" stroke="#fff" stroke-width="1.6"/></svg></span><div><div class="lbl">Mail:</div><div class="val">service@varnoelectrical-example.com.au</div></div></div>
</div>

<div class="abs" style="left:814px;top:2820px;width:286px">
  <div class="f-head">CONTACT FORM</div><div class="f-rule"></div>
  <div style="display:flex;gap:10px;margin-top:22px"><div class="field" style="width:138px;height:36px">Name</div><div class="field" style="width:138px;height:36px">Phone</div></div>
  <div class="field" style="height:66px;margin-top:8px">Message</div>
  <div style="margin-top:14px"><span class="send">SEND MESSAGE</span></div>
</div>

<div class="abs copy-bar"></div>
<div class="abs copy-text">Copyright © 2017 Varno Electrical. All Rights Reserved.</div>
<div class="abs copy-socials"><span></span><span></span><span></span><span></span><span></span></div>

</body>
</html>
```